Companybrochure for Consulting & Financing Firm

I need to have a Company Brochure asap for our company. We have a website that describes what we do, but we need also a brochure, that can be sent by PDF of eventually be printed as well.

The brochure should be short but nice and appealing to the customers.

We provide professional management consulting and help our customers to get finance for very diferent projects. Our business has a lot to do with personal relations, but also we are very professional in the way we work and how develop the solutions for our clients. Our clients are mainly government-owned firm, but also private trading companies and wealthy private investors.

Our customers are mainly in Latin America, but the company is headquater is in Switzerland. We are opening offices in Panama and Caracas, this should be easaly be adabtable later.

Please have a look at our website www.vorelpartners.ch. In the brochure, we would segment our services in 1.) Project Developments 2.) Management Conulting 3.) Investment Management and 4.) Finance Solutions.

Also do have a look at www.vorelpartners.ch
(Click E for the English version)
Updates

I managed to put the Mock-Up to the Website.
It is actually not really a mock-up, it is a version I have designed myself.
Well as I am not a designer, I hope you can make it much better.
The content however is what I would put in any other design as well.

Target Market(s)

Top Management, Investors, Entrepreneurs, Government Officials

Industry/Entity Type

Management Consulting

Requirements
Must have
• Design should reflect this image elements:

We are entrepreneurs.
We are comitted to get things done.
We work closely with the client side by side.
We are a professional partner.
We are not afraid of delivering unconventional solutions.
We look at the problem from various angles.
We analyse, develop solutions and implent results.
Should not have
• Typical US-American style elements. We do not want to give the impression of being a US company.

We do not want to appear to be neo-liberal. We are a politically neutral professional consulting firm.

```html
<!DOCTYPE html>
<html lang="en">
<head>
<meta charset="utf-8">
<title>Brochure Spread – Management Consulting &amp; Investment Management</title>
<link rel="stylesheet" href="https://fonts.googleapis.com/css2?family=Open+Sans:wght@400;600;700&display=swap">
<style>
  :root {
    --backdrop: #e9e6e1;
    --paper: #f4f5f7;
    --paper-shade: #e3e5ea;
    --blue: #2f7fc1;
    --blue-light: #4c9bd8;
    --blue-dark: #1f4f86;
    --navy: #283f6b;
    --rule: #2a5d97;
    --white: #ffffff;
  }
  * { box-sizing: border-box; margin: 0; padding: 0; }
  html, body {
    width: 1200px; height: 900px; overflow: hidden;
    background: var(--backdrop);
    font-family: "Open Sans", Arial, sans-serif;
  }
  .spread {
    position: absolute; left: 40px; top: 230px;
    width: 1120px; height: 440px;
    display: flex;
    box-shadow: 0 10px 30px rgba(0,0,0,.18);
  }
  .page {
    position: relative; width: 560px; height: 440px;
    background: var(--paper); overflow: hidden;
  }
  .page--left { background: linear-gradient(90deg, var(--paper) 85%, var(--paper-shade)); }
  .page--right { background: linear-gradient(270deg, var(--paper) 85%, var(--paper-shade)); }

  .photo { position: absolute; }
  .photo--team {
    left: 24px; top: 50px; width: 380px; height: 210px;
    background: linear-gradient(90deg, #8d9099 0%, #c7ccd4 45%, #eef1f5 85%, rgba(244,245,247,0) 100%);
  }
  .photo--eagle {
    left: 36px; top: 24px; width: 350px; height: 200px; border-radius: 14px;
    background: linear-gradient(180deg, #d9a9c4 0%, #9b87b8 35%, #6b5a78 60%, #4c4a3a 100%);
  }

  .service-panel {
    position: absolute; border-radius: 12px; overflow: hidden;
    background: linear-gradient(180deg, var(--blue-light), var(--blue));
    color: var(--white);
    box-shadow: 0 2px 6px rgba(0,0,0,.15);
  }
  .service-panel--consulting { left: 196px; top: 130px; width: 340px; height: 180px; }
  .service-panel--investment { left: 210px; top: 130px; width: 320px; height: 118px; }
  .service-panel__title {
    background: linear-gradient(180deg, #3a5a8e, var(--navy));
    font-weight: 700; font-size: 15px; letter-spacing: .2px;
    padding: 6px 14px; border-radius: 12px 12px 0 0;
  }
  .service-panel__body { padding: 10px 14px; font-size: 8.4px; line-height: 1.35; }
  .service-panel__body p { margin-bottom: 8px; }
  .service-panel__principle { text-align: right; font-weight: 700; }

  .page-rule { position: absolute; left: 0; bottom: 0; width: 560px; height: 60px; }
  .page-number {
    position: absolute; bottom: 16px; width: 22px; height: 20px;
    background: var(--blue-dark); color: var(--white);
    font-size: 12px; font-weight: 700; text-align: center; line-height: 20px;
  }
  .page--left .page-number { left: 14px; }
  .page--right .page-number { right: 14px; }
</style>
</head>
<body>
  <main class="spread">
    <section class="page page--left">
      <div class="photo photo--team" role="img" aria-label="Photo of a consulting team reviewing documents in a bright office"></div>
      <article class="service-panel service-panel--consulting">
        <h2 class="service-panel__title">&gt;&gt; Management Consulting</h2>
        <div class="service-panel__body">
          <p>We elaborate solutions together with our customers and business partners by assisting owners and top management in structured decision making.</p>
          <p>We work goal-oriented following the principle:<br><span class="service-panel__principle" style="display:block">&gt;Analysis &gt;&gt; Solutions &gt;&gt;&gt; Results.</span></p>
          <p>Our consulting team members do all have many years of experience from previous assignments at leading international management consulting companies and are familiar with methodologies used in management consulting. We complete the team of consultants with the appropriate subject matter experts.</p>
        </div>
      </article>
      <svg class="page-rule" viewBox="0 0 560 60" aria-hidden="true">
        <path d="M36 50 Q300 44 560 20" fill="none" stroke="var(--rule)" stroke-width="2"/>
      </svg>
      <div class="page-number">3</div>
    </section>

    <section class="page page--right">
      <div class="photo photo--eagle" role="img" aria-label="Photo of an eagle perched above a mountain valley at sunrise"></div>
      <article class="service-panel service-panel--investment">
        <h2 class="service-panel__title">&gt;&gt; Investment Management</h2>
        <div class="service-panel__body">
          <p>Sometimes a project with high potential has to be developed before its economic value becomes apparent.</p>
          <p>In such situations, we participate financially in the project and commit ourselves as entrepreneurs together with the owners.</p>
          <p>We also take care of project management.</p>
        </div>
      </article>
      <svg class="page-rule" viewBox="0 0 560 60" aria-hidden="true">
        <path d="M0 22 Q260 44 524 50" fill="none" stroke="var(--rule)" stroke-width="2"/>
      </svg>
      <div class="page-number">4</div>
    </section>
  </main>
</body>
</html>
```